Professional & attention grabbing.

A business card design, front and back. I already have a logo I will attach, but I am open to something new as well.
Things to include:
Name:
Title:
Phone:
Email:
Wanting something that is professional but attention grabbing.
Also we do a lot of work using drones on natural gas pipelines (leading the future)if you want to include any of that. I'm open to ideas.
Target Market(s)
Natural gas transmission industry / greenhouse gas mitigation industry
Industry/Entity Type
Business
Colors
Designer to choose colors to be used in the design.
Look and feel
Each slider illustrates characteristics of the customer's brand and the style your logo design should communicate.

```html
<!DOCTYPE html>
<html lang="en">
<head>
<meta charset="utf-8">
<title>Harrow Inspections — Business Card</title>
<link rel="stylesheet" href="https://fonts.googleapis.com/css2?family=Open+Sans:ital,wght@0,400;0,700;1,400&family=Roboto+Condensed:wght@400&display=swap">
<style>
  :root {
    --backdrop: #e4e4e4;
    --card-white: #ffffff;
    --charcoal: #38383a;
    --brand-red: #be1e24;
    --text-grey: #4a4a4c;
    --text-light: #ffffff;
  }
  * { box-sizing: border-box; margin: 0; padding: 0; }
  html, body { width: 1200px; height: 987px; overflow: hidden; }
  body {
    background: var(--backdrop);
    font-family: "Open Sans", Arial, sans-serif;
    position: relative;
  }
  .card {
    position: absolute;
    left: 293px;
    width: 615px;
    height: 352px;
    overflow: hidden;
  }
  .card--front { top: 130px; background: var(--card-white); }
  .card--back { top: 505px; background: var(--charcoal); }

  /* Front */
  .name-band {
    position: absolute;
    left: 0; top: 49px;
    width: 349px; height: 86px;
    background: var(--charcoal);
    padding: 16px 0 0 33px;
  }
  .name-band__name {
    color: var(--brand-red);
    font-size: 20px;
    line-height: 24px;
    text-transform: uppercase;
  }
  .name-band__title {
    color: var(--text-light);
    font-size: 16px;
    line-height: 26px;
    text-transform: uppercase;
  }
  .brand-lockup {
    position: absolute;
    left: 356px; top: 49px;
    height: 86px;
    display: flex;
    align-items: center;
    gap: 12px;
  }
  .brand-lockup__mark { width: 52px; height: 52px; background: var(--brand-red); }
  .brand-lockup__name {
    font-weight: 700;
    font-size: 22px;
    line-height: 26px;
    color: var(--charcoal);
  }
  .contact {
    position: absolute;
    left: 0; right: 0; top: 272px;
    text-align: center;
    color: var(--text-grey);
    font-size: 16px;
    line-height: 24px;
  }
  .contact__row { display: flex; justify-content: center; align-items: center; gap: 6px; }
  .contact__row svg { width: 14px; height: 14px; fill: var(--brand-red); }
  .contact__gap { width: 6px; }

  /* Back */
  .back-block {
    position: absolute;
    left: 268px; top: 7px;
    width: 339px; height: 339px;
    background: var(--brand-red);
  }
  .back-brand {
    position: absolute;
    left: 30px; top: 212px;
    width: 225px;
    color: var(--text-light);
    font-weight: 700;
    font-size: 58px;
    line-height: 64px;
    white-space: nowrap;
  }
  .back-tagline {
    position: absolute;
    left: 30px; top: 283px;
    color: var(--text-light);
    font-family: "Roboto Condensed", "Arial Narrow", sans-serif;
    font-size: 17px;
    line-height: 20px;
    text-transform: uppercase;
    white-space: nowrap;
  }
  .back-url {
    position: absolute;
    left: 30px; top: 310px;
    color: var(--text-light);
    font-style: italic;
    font-size: 14px;
    line-height: 18px;
    letter-spacing: 2px;
    white-space: nowrap;
  }
</style>
</head>
<body>
  <section class="card card--front">
    <div class="name-band">
      <p class="name-band__name">Dana Hale</p>
      <p class="name-band__title">CEO/Founder</p>
    </div>
    <div class="brand-lockup">
      <span class="brand-lockup__mark"></span>
      <span class="brand-lockup__name">Harrow<br>Inspections</span>
    </div>
    <div class="contact">
      <p class="contact__row">
        <svg viewBox="0 0 24 24" aria-hidden="true"><path d="M6.6 10.8a15 15 0 0 0 6.6 6.6l2.2-2.2c.3-.3.7-.4 1-.2 1.1.4 2.3.6 3.6.6.6 0 1 .4 1 1V20c0 .6-.4 1-1 1A17 17 0 0 1 3 4c0-.6.4-1 1-1h3.5c.6 0 1 .4 1 1 0 1.3.2 2.5.6 3.6.1.3 0 .7-.2 1z"/></svg>
        <span>555 014 2290</span>
        <span class="contact__gap"></span>
        <svg viewBox="0 0 24 24" aria-hidden="true"><path d="M2 5h20v14H2z M2 5l10 8 10-8" /></svg>
        <span>dana@harrowinspect.com</span>
      </p>
      <p class="contact__row">
        <svg viewBox="0 0 24 24" aria-hidden="true"><circle cx="12" cy="12" r="10"/></svg>
        <span>www.harrowinspect.com</span>
      </p>
    </div>
  </section>

  <section class="card card--back">
    <div class="back-block"></div>
    <p class="back-brand">Harrow</p>
    <p class="back-tagline">Inspections</p>
    <p class="back-url">www.harrowinspect.com</p>
  </section>
</body>
</html>
```